Very visible CoWorking Building Sign overlooking downtown LA and 110 freeway

Our building is drab but very visible and in the best location. We need a great sign for our monolith that overlooks downtown LA and the 100 freeway. We are a new CoWorking business and would like to have a few things we do on the sign: private offices, virtual offices, CoWorking Lounge. Everything we have seen is ho-hum. Can you get us noticed? We need people to know what we do and that we are here but in a creative, professional, unique sign.
Target Market(s)
People who have a business in DTLA, remote workers and those who work from home who need a professional address.
Requirements
Must have
- Our logo (which can be somewhat reimagined) which has our address 2417 on it. The three things we focus on: Private Offices, Virtual Offices, CoWorking Lounge. Incorporate some Navy. Readable from several hundred feet away.
Nice to have
- Mural feel? Something inspirational in this crazy COVID times? Graphics? Color block. I like the idea of decorative but it has to be readable as a building sign. The same with the use of colors. Our colors are grays and navy but with a pop of the chartreuse (we have 2 velvet chartreuse chairs in the space). Helpful to view our website: Harborview2417.com.
Should not have
- Not too graffiti. Keep it professional but unique and wow.

```html
<!DOCTYPE html>
<html lang="en">
<head>
<meta charset="utf-8">
<title>2417 Harborview – Building Banner</title>
<link rel="stylesheet" href="https://fonts.googleapis.com/css2?family=Alfa+Slab+One&display=swap">
<style>
  :root {
    --navy: #1f2d4f;
    --navy-deep: #17223d;
    --gray-light: #d6d7d8;
    --gray-mid: #b9babc;
    --gray-band: #8e8f91;
    --bar-dark: #2a2b2e;
    --photo-warm: #8a6a45;
    --white: #f4f4f4;
  }
  html, body {
    margin: 0;
    padding: 0;
    width: 800px;
    height: 1200px;
    overflow: hidden;
    background: var(--gray-light);
  }
  .banner {
    position: relative;
    width: 800px;
    height: 1200px;
    background: radial-gradient(ellipse at 50% 70%, var(--gray-light) 0%, var(--gray-mid) 100%);
    font-family: "Alfa Slab One", Georgia, serif;
    color: var(--navy);
  }
  .banner-art {
    position: absolute;
    inset: 0;
  }
  .brand-name {
    position: absolute;
    top: 665px;
    left: 0;
    width: 800px;
    text-align: center;
    font-size: 58px;
    line-height: 1;
    letter-spacing: 2px;
    margin: 0;
    font-weight: 400;
  }
  .services {
    position: absolute;
    left: 0;
    width: 800px;
    text-align: center;
    margin: 0;
    font-size: 50px;
    line-height: 1.1;
    font-weight: 400;
    letter-spacing: 1px;
  }
  .services-offices { top: 812px; }
  .services-lounge { top: 966px; }
</style>
</head>
<body>
<main class="banner">
  <svg class="banner-art" width="800" height="1200" viewBox="0 0 800 1200">
    <defs>
      <linearGradient id="interiorTone" x1="0" y1="0" x2="0" y2="1">
        <stop offset="0" stop-color="#9aa0a6"/>
        <stop offset="0.55" stop-color="#a58a66"/>
        <stop offset="1" stop-color="#8a6a45"/>
      </linearGradient>
      <linearGradient id="circleToneA" x1="0" y1="0" x2="1" y2="1">
        <stop offset="0" stop-color="#b9b2a6"/>
        <stop offset="1" stop-color="#6d5a46"/>
      </linearGradient>
      <linearGradient id="circleToneB" x1="0" y1="0" x2="1" y2="1">
        <stop offset="0" stop-color="#d8d8d2"/>
        <stop offset="1" stop-color="#8e9a8a"/>
      </linearGradient>
    </defs>

    <polygon class="interior-photo" points="0,0 800,0 800,615 0,505"
             fill="url(#interiorTone)" role="img"
             aria-label="Photo of the coworking floor with long white desks, bar stools and polished wood floor"/>
    <polygon class="navy-block" points="0,0 800,0 800,280 0,140" fill="var(--navy-deep)" opacity="0.85"/>

    <circle cx="180" cy="160" r="122" fill="var(--white)"/>
    <circle cx="180" cy="160" r="112" fill="url(#circleToneA)" role="img"
            aria-label="Photo of the kitchen counter with bar stools"/>
    <circle cx="540" cy="200" r="122" fill="var(--white)"/>
    <circle cx="540" cy="200" r="112" fill="url(#circleToneB)" role="img"
            aria-label="Photo of a private office with desk chair and plant"/>

    <!-- rule under name -->
    <line class="name-rule" x1="0" y1="790" x2="800" y2="776" stroke="var(--navy)" stroke-width="3" opacity="0.7"/>
    <!-- rule between services -->
    <line class="services-rule" x1="150" y1="946" x2="660" y2="940" stroke="var(--navy)" stroke-width="2" opacity="0.6"/>

    <polygon class="bottom-band" points="20,1150 760,1150 780,1100 40,1100" fill="var(--gray-band)"/>
    <rect class="bottom-bar" x="0" y="1160" width="800" height="40" fill="var(--bar-dark)"/>
  </svg>

  <h1 class="brand-name">2417 HARBORVIEW</h1>
  <p class="services services-offices">PRIVATE &amp; VIRTUAL<br>OFFICES</p>
  <p class="services services-lounge">COWORKING<br>LOUNGE</p>
</main>
</body>
</html>
```